Design a New Business Card for Our Company

We are looking for fresh, unique, and a modern business card that reflects our roots as digital marketing agency focused on SEM.

Industry/Entity Type

Marketing

Contact Information for Business Card

looking for very unique out of the box designs. clean and modern that compliments our logo

Requirements
Must have
• colors should match our logo
• Front should have name, address, email, and phone/fax of the person, phone/fax are the same number
• back should have our url

```html
<!DOCTYPE html>
<html lang="en">
<head>
<meta charset="utf-8">
<title>Lumora Solutions Business Card</title>
<link rel="stylesheet" href="https://fonts.googleapis.com/css2?family=Open+Sans:wght@400;600&display=swap">
<style>
  :root {
    --backdrop: #3b3b3b;
    --card-front: #ffffff;
    --card-back: #b3b3b3;
    --ink-grey: #9d9fa2;
    --ink-dark: #4d4d4d;
    --accent-blue: #5b9bd5;
    --icon-grey: #a6a8ab;
    --white: #ffffff;
  }
  * { margin: 0; padding: 0; box-sizing: border-box; }
  html, body {
    width: 1105px; height: 1200px; overflow: hidden;
    background: var(--backdrop);
    font-family: "Open Sans", Arial, sans-serif;
  }
  .canvas { position: relative; width: 1105px; height: 1200px; }
  .card {
    position: absolute; left: 196px; width: 720px; height: 411px;
  }
  .card--front { top: 146px; background: var(--card-front); }
  .card--back { top: 602px; background: var(--card-back); }

  .holder { position: absolute; right: 50px; top: 42px; text-align: right; }
  .holder__name { font-size: 25px; font-weight: 600; color: var(--ink-grey); line-height: 1.2; }
  .holder__title { font-size: 19px; color: var(--accent-blue); line-height: 1.3; }
  .accent-tab {
    position: absolute; right: 0; top: 46px; width: 17px; height: 52px;
    background: var(--accent-blue);
  }

  .brand {
    position: absolute; left: 49px; top: 172px;
    font-size: 46px; font-weight: 600; color: var(--ink-grey);
    letter-spacing: -1px; line-height: 1;
  }

  .contact { position: absolute; left: 49px; top: 288px; list-style: none; }
  .contact li {
    display: flex; align-items: center; gap: 10px;
    font-size: 19px; color: var(--ink-dark); line-height: 27px;
  }
  .contact svg { width: 18px; height: 18px; fill: var(--icon-grey); flex: none; }

  .address {
    position: absolute; right: 50px; top: 314px; text-align: right;
    font-style: normal; font-size: 19px; color: var(--ink-dark); line-height: 27px;
  }

  .back-brand {
    position: absolute; right: 50px; top: 262px; text-align: right;
    color: var(--white);
  }
  .back-brand__name { font-size: 52px; font-weight: 600; letter-spacing: -1px; line-height: 1.1; }
  .back-brand__url { font-size: 18px; letter-spacing: 4px; margin-top: 10px; }
</style>
</head>
<body>
<main class="canvas">
  <section class="card card--front" aria-label="Card front">
    <div class="holder">
      <p class="holder__name">Daniel Mercer</p>
      <p class="holder__title">CEO/Founder</p>
    </div>
    <div class="accent-tab"></div>

    <p class="brand">Lumora Solutions</p>

    <ul class="contact">
      <li>
        <svg viewBox="0 0 24 24" aria-hidden="true"><path d="M6.6 10.8a15.1 15.1 0 0 0 6.6 6.6l2.2-2.2a1 1 0 0 1 1-.25 11.4 11.4 0 0 0 3.6.57 1 1 0 0 1 1 1V20a1 1 0 0 1-1 1A17 17 0 0 1 3 4a1 1 0 0 1 1-1h3.5a1 1 0 0 1 1 1c0 1.25.2 2.45.57 3.6a1 1 0 0 1-.25 1z"/></svg>
        555 214 3870
      </li>
      <li>
        <svg viewBox="0 0 24 24" aria-hidden="true"><path d="M6 2h10l2 2v5H6z M3 10h18v8h-3v4H6v-4H3z M8 16v4h8v-4z"/></svg>
        555 214 3871
      </li>
      <li>
        <svg viewBox="0 0 24 24" aria-hidden="true"><path d="M2 5h20v14H2z M3.5 6.5v1l8.5 5.5 8.5-5.5v-1z"/></svg>
        hello@lumora.com
      </li>
    </ul>

    <address class="address">
      112 Harbor View Road<br>
      Portland, Oregon 97205
    </address>
  </section>

  <section class="card card--back" aria-label="Card back">
    <div class="back-brand">
      <p class="back-brand__name">Lumora Solutions</p>
      <p class="back-brand__url">www.lumora.com</p>
    </div>
  </section>
</main>
</body>
</html>
```